VENTURE CAPITAL GROUP BUSINESS CARD DESIGN

Venture Capital Group based in SF looking for a bold business card design. No trendy colour explosion, 3D effects etc. Just "simple" optical effects. Works on your brain, keeps your eye focused and sticks to your mind.
Target Market(s)
Technology startups
Industry/Entity Type
Venture Capital
Contact Information for Business Card
DESMOND WHITLAKE
MANAGING PARTNER
187 FENWORTH ST SAN FRANCISCO, CA 94187
415.555.0142 O
415.555.0147 F
415.555.0193 C
desmond@veldtmoorcapital.ventures

```html
<!DOCTYPE html>
<html lang="en">
<head>
<meta charset="utf-8">
<title>Veldtmoor Capital Group — Business Card</title>
<link rel="stylesheet" href="https://fonts.googleapis.com/css2?family=Cinzel:wght@500&family=EB+Garamond:wght@400;700&display=swap">
<style>
  :root {
    --stage: #1f1f1f;
    --card-white: #fbfbfb;
    --brand-green: #1f8f3a;
    --band-green: #23923e;
    --band-text: #e6f3e8;
    --ink: #2b2b2b;
    --divider: #b9b9b9;
    --facet-light: #f4f4f4;
    --facet-mid: #dcdcdc;
  }
  * { box-sizing: border-box; margin: 0; padding: 0; }
  html, body { width: 1200px; height: 873px; overflow: hidden; }
  body {
    background: var(--stage);
    display: flex;
    align-items: center;
    justify-content: center;
    gap: 30px;
    font-family: "EB Garamond", Georgia, serif;
  }
  .card {
    position: relative;
    width: 560px;
    height: 320px;
    background: var(--card-white);
    overflow: hidden;
  }

  /* Back side */
  .card-back .facet-field {
    position: absolute; inset: 0;
    background: linear-gradient(135deg, var(--facet-light) 0%, var(--facet-mid) 45%, var(--facet-light) 70%, var(--facet-mid) 100%);
  }
  .card-back .brand-name {
    position: absolute; left: 0; right: 0; top: 140px;
    text-align: center;
    font-family: "Cinzel", "Times New Roman", serif;
    font-weight: 500;
    font-size: 30px;
    letter-spacing: 1px;
    color: var(--brand-green);
  }

  /* Front side */
  .card-front .brand-name {
    position: absolute; left: 0; right: 0; top: 58px;
    text-align: center;
    font-family: "Cinzel", "Times New Roman", serif;
    font-weight: 500;
    font-size: 18px;
    letter-spacing: 1px;
    color: var(--brand-green);
  }
  .person {
    position: absolute; right: 312px; top: 128px;
    text-align: right;
  }
  .person-name { font-weight: 700; font-size: 19px; color: var(--brand-green); line-height: 1.1; }
  .person-title { font-size: 14px; color: var(--ink); }
  .divider {
    position: absolute; left: 268px; top: 106px;
    width: 2px; height: 62px;
    background: linear-gradient(var(--card-white), var(--divider), var(--card-white));
  }
  .contact-list {
    position: absolute; left: 284px; top: 106px;
    list-style: none;
    font-size: 14px; color: var(--ink); line-height: 21px;
  }
  .contact-list li { display: flex; align-items: center; gap: 7px; }
  .contact-list svg { width: 12px; height: 12px; fill: var(--brand-green); flex: none; }

  .band {
    position: absolute; left: 0; right: 0; bottom: 0; height: 128px;
    background: var(--band-green);
    color: var(--band-text);
  }
  .band-title {
    display: flex; align-items: center; justify-content: center; gap: 10px;
    margin-top: 16px;
    font-weight: 700; font-size: 15px; letter-spacing: 1px;
  }
  .band-title::before, .band-title::after {
    content: ""; width: 48px; height: 1px; background: var(--band-text);
  }
  .band-line {
    display: flex; justify-content: center; gap: 22px;
    margin-top: 10px; font-size: 14px;
  }
  .band-line span { display: flex; align-items: center; gap: 6px; }
  .band-line svg { width: 13px; height: 13px; fill: var(--band-text); }
  .band-web { text-align: center; margin-top: 8px; font-size: 14px; letter-spacing: 1px; }
</style>
</head>
<body>

<section class="card card-back">
  <div class="facet-field" role="img" aria-label="Light grey faceted polygon background pattern"></div>
  <p class="brand-name">VELDTMOOR CAPITAL GROUP</p>
</section>

<section class="card card-front">
  <p class="brand-name">VELDTMOOR CAPITAL GROUP</p>

  <div class="person">
    <p class="person-name">Desmond Whitlake</p>
    <p class="person-title">Managing Partner</p>
  </div>

  <div class="divider"></div>

  <ul class="contact-list">
    <li><svg viewBox="0 0 24 24"><path d="M6.6 10.8a15 15 0 0 0 6.6 6.6l2.2-2.2a1 1 0 0 1 1-.25 11.4 11.4 0 0 0 3.6.57 1 1 0 0 1 1 1V20a1 1 0 0 1-1 1A17 17 0 0 1 3 4a1 1 0 0 1 1-1h3.5a1 1 0 0 1 1 1c0 1.25.2 2.45.57 3.57a1 1 0 0 1-.25 1z"/></svg>415.555.0147</li>
    <li><svg viewBox="0 0 24 24"><path d="M6 3h12v5H6zM4 9h16a2 2 0 0 1 2 2v6h-4v4H6v-4H2v-6a2 2 0 0 1 2-2zm4 7v3h8v-3z"/></svg>415.555.0193</li>
    <li><svg viewBox="0 0 24 24"><path d="M2 5h20v14H2zm2 2v.5l8 5.5 8-5.5V7l-8 5.5z"/></svg>desmond@veldtmoorcapital.ventures</li>
  </ul>

  <div class="band">
    <p class="band-title">VELDTMOOR CAPITAL GROUP</p>
    <p class="band-line">
      <span><svg viewBox="0 0 24 24"><path d="M6.6 10.8a15 15 0 0 0 6.6 6.6l2.2-2.2a1 1 0 0 1 1-.25 11.4 11.4 0 0 0 3.6.57 1 1 0 0 1 1 1V20a1 1 0 0 1-1 1A17 17 0 0 1 3 4a1 1 0 0 1 1-1h3.5a1 1 0 0 1 1 1c0 1.25.2 2.45.57 3.57a1 1 0 0 1-.25 1z"/></svg>415.555.0142</span>
      <span><svg viewBox="0 0 24 24"><path d="M12 2a7 7 0 0 0-7 7c0 5 7 13 7 13s7-8 7-13a7 7 0 0 0-7-7zm0 9.5A2.5 2.5 0 1 1 12 6.5a2.5 2.5 0 0 1 0 5z"/></svg>187 Fenworth St San Francisco, CA 94187</span>
    </p>
    <p class="band-web">www.veldtmoorcapital.ventures</p>
  </div>
</section>

</body>
</html>
```